Lawn care business card

I am looking for a quality designed personal business card to represent the quality and elegant nature of our company. We separate ourselves in our market by the aesthetic value of our work, so I am looking for marketing material that does the same. We target our marketing high end customers, and we try to avoid price shoppers. I am open to all design options, so long as they are in line with our companies values.

We are tend to go with a retro look on everything from our logo and print material, to our uniforms. We like to portray and "old fashion" set of core values, with a modern elegance. So a wild and crazy look is out of the question.

Things I'd like on the card:
1.) Logo
2.) Phone number: (816) 555-2931
3.) Website: Verdelynkc.com
4.) Email: robertfairley@verdelynkc.com
5.) My name: Robert Fairley
6.) Facebook link: facebook.com/VerdelynGardenandGrounds
7.) Instagram: http://instagram.com/verdelynkc

Attached is a copy of our logo.

Reason: More time is needed to gather conclusive feedback from the members of our marketing team.

```html
<!DOCTYPE html>
<html lang="en">
<head>
<meta charset="utf-8">
<title>Verdelyn Business Card</title>
<link rel="stylesheet" href="https://fonts.googleapis.com/css2?family=Lato:wght@400;700&family=Open+Sans:wght@400;600;700&display=swap">
<style>
  :root {
    --stage: #2e2e2e;
    --card: #f7f7f7;
    --card-edge: #e4e4e4;
    --accent: #e8591c;
    --ink: #2b2b2b;
    --ink-soft: #3a3a3a;
    --rule: #5c5c5c;
  }
  * { margin: 0; padding: 0; box-sizing: border-box; }
  html, body {
    width: 1200px;
    height: 1116px;
    overflow: hidden;
    background: var(--stage);
  }
  .business-card {
    position: absolute;
    left: 100px;
    top: 272px;
    width: 1000px;
    height: 572px;
    border-radius: 36px;
    background: linear-gradient(160deg, #ffffff 0%, var(--card) 60%, var(--card-edge) 100%);
    box-shadow: 0 18px 40px rgba(0,0,0,0.45);
    font-family: "Open Sans", sans-serif;
  }
  .info-block {
    position: absolute;
    left: 70px;
    padding-left: 26px;
  }
  .info-block::before {
    content: "";
    position: absolute;
    left: 0;
    bottom: 4px;
    width: 9px;
    height: 34px;
    background: var(--rule);
  }
  .identity { top: 128px; }
  .holder-name {
    font-family: "Lato", sans-serif;
    font-weight: 400;
    font-size: 30px;
    line-height: 1.1;
    color: var(--accent);
  }
  .holder-role {
    font-family: "Open Sans", sans-serif;
    font-weight: 600;
    font-size: 19px;
    color: var(--ink);
  }
  .social { top: 248px; }
  .social-link {
    display: block;
    font-weight: 700;
    font-size: 24px;
    line-height: 1.2;
    color: var(--accent);
  }
  .contact { top: 378px; }
  .contact::before { height: 78px; }
  .contact-line {
    display: block;
    font-weight: 600;
    font-size: 22px;
    line-height: 1.45;
    color: var(--ink-soft);
  }
  .contact-web {
    font-weight: 700;
    font-size: 26px;
    color: var(--ink);
  }
  .contact-web .domain { color: var(--accent); }
  .brand-mark {
    position: absolute;
    right: 80px;
    top: 236px;
    display: flex;
    align-items: center;
    gap: 18px;
  }
  .brand-dot {
    width: 48px;
    height: 48px;
    border-radius: 50%;
    background: var(--accent);
  }
  .brand-name {
    font-family: "Open Sans", sans-serif;
    font-weight: 700;
    font-size: 54px;
    letter-spacing: 2px;
    color: var(--ink);
  }
</style>
</head>
<body>
  <div class="business-card">
    <div class="info-block identity">
      <p class="holder-name">Robert Fairley</p>
      <p class="holder-role">Owner / Founder</p>
    </div>

    <div class="info-block social">
      <span class="social-link">fb.com/VerdelynGardenandGrounds</span>
      <span class="social-link">instagram.com/verdelynkc</span>
    </div>

    <div class="info-block contact">
      <span class="contact-line">(816) 555-2931</span>
      <span class="contact-line">robertfairley@verdelynkc.com</span>
      <span class="contact-line contact-web">www.<span class="domain">Verdelynkc</span>.com</span>
    </div>

    <div class="brand-mark">
      <span class="brand-dot"></span>
      <span class="brand-name">VERDELYN</span>
    </div>
  </div>
</body>
</html>
```